Moravel Aesthetic Doctor

I require an elegant, luxurious looking business card for my aesthetic business. I am a doctor and that will set me aside from competitors. I am planning to provide home and spa based treatments to clients with high expectations. I have attached my logo.

```html
<!DOCTYPE html>
<html lang="en">
<head>
<meta charset="utf-8">
<title>Moravel Aesthetic Doctor – Business Card</title>
<link rel="stylesheet" href="https://fonts.googleapis.com/css2?family=Montserrat:wght@400;500&display=swap">
<style>
  :root {
    --backdrop: #dcdde1;
    --card: #fbfbfb;
    --ink: #2f3033;
    --brand-grey: #8d8f93;
    --brand-blue: #3a8fd0;
    --brand-sky: #7cc3ea;
    --rule: #3a8fd0;
  }
  * { margin: 0; padding: 0; box-sizing: border-box; }
  html, body {
    width: 1200px; height: 800px; overflow: hidden;
    background: var(--backdrop);
    font-family: "Montserrat", sans-serif;
    color: var(--ink);
  }
  .canvas { position: relative; width: 1200px; height: 800px; }
  .card {
    position: absolute; left: 370px; width: 460px; height: 263px;
    background: var(--card);
    box-shadow: -6px 14px 18px rgba(0,0,0,0.18);
  }
  .card--front { top: 93px; }
  .card--back { top: 422px; }

  .wordmark { position: absolute; display: flex; align-items: center; gap: 10px; }
  .wordmark__dot {
    border-radius: 50%; background: var(--brand-sky); flex: none;
  }
  .wordmark__name {
    font-weight: 400; color: var(--brand-grey);
    text-transform: uppercase; line-height: 1.05;
  }
  .wordmark__name span { display: block; }

  .card--front .wordmark { left: 95px; top: 56px; }
  .card--front .wordmark__dot { width: 64px; height: 64px; }
  .card--front .wordmark__name .line-main { font-size: 38px; letter-spacing: 2px; }
  .card--front .wordmark__name .line-sub { font-size: 15.5px; letter-spacing: 1.6px; margin-top: 2px; }

  .services {
    position: absolute; left: 0; right: 0; top: 184px;
    text-align: center; font-size: 11.4px; line-height: 13.5px;
  }
  .tagline {
    position: absolute; left: 0; right: 0; top: 214px;
    text-align: center; font-size: 14.8px; color: var(--brand-blue);
  }

  .card--back .wordmark { left: 43px; top: 105px; gap: 8px; }
  .card--back .wordmark__dot { width: 48px; height: 48px; }
  .card--back .wordmark__name .line-main { font-size: 23px; letter-spacing: 1.2px; }
  .card--back .wordmark__name .line-sub { font-size: 9.6px; letter-spacing: 1px; margin-top: 2px; }

  .divider {
    position: absolute; left: 237px; top: 85px; width: 1px; height: 93px;
    background: var(--rule);
  }
  .contact { position: absolute; left: 250px; top: 82px; }
  .contact__name { font-size: 15px; font-weight: 400; }
  .contact__name small { font-size: 7px; color: var(--brand-blue); margin-left: 2px; }
  .contact__credential {
    margin-top: 4px; font-size: 10.6px; line-height: 13px; color: var(--brand-blue);
  }
  .contact__list { list-style: none; margin-top: 9px; font-size: 10.8px; line-height: 14px; }
  .contact__list li { display: flex; align-items: center; gap: 6px; }
  .contact__list svg { width: 8px; height: 8px; flex: none; }
  .social { display: inline-flex; gap: 6px; margin-left: 16px; }
  .social i { width: 8px; height: 8px; border-radius: 50%; background: var(--brand-blue); display: block; }
</style>
</head>
<body>
<main class="canvas">
  <section class="card card--front">
    <div class="wordmark">
      <div class="wordmark__dot"></div>
      <h1 class="wordmark__name"><span class="line-main">Moravel</span><span class="line-sub">Aesthetic Doctor</span></h1>
    </div>
    <p class="services">Dermal injectables - Plasma facials - Microneedling<br>Skin boosters - Excessive sweating</p>
    <p class="tagline">Home and Spa Based Treatments</p>
  </section>

  <section class="card card--back">
    <div class="wordmark">
      <div class="wordmark__dot"></div>
      <h2 class="wordmark__name"><span class="line-main">Moravel</span><span class="line-sub">Aesthetic Doctor</span></h2>
    </div>
    <div class="divider"></div>
    <div class="contact">
      <p class="contact__name">Dr Elise Varden <small>MRCPCH MD</small></p>
      <p class="contact__credential">Australasian Diploma<br>of Aesthetic Medicine</p>
      <ul class="contact__list">
        <li><svg viewBox="0 0 10 10" aria-hidden="true"><path d="M2 0.5 L4 2.8 L3 4 Q4.3 6 6 7 L7.2 6 L9.5 8 L8 9.5 Q2.5 8.5 0.5 2 Z" fill="#3a8fd0"/></svg>0800 555 014</li>
        <li><svg viewBox="0 0 10 10" aria-hidden="true"><rect x="0.5" y="2" width="9" height="6.5" fill="#3a8fd0"/><path d="M0.5 2 L5 5.8 L9.5 2" stroke="#fff" stroke-width="0.9" fill="none"/></svg>elise@moravel.co.nz</li>
        <li><svg viewBox="0 0 10 10" aria-hidden="true"><circle cx="5" cy="5" r="4.3" fill="none" stroke="#8d8f93" stroke-width="0.9"/><path d="M0.7 5 H9.3 M5 0.7 V9.3 M5 0.7 Q2 5 5 9.3 M5 0.7 Q8 5 5 9.3" stroke="#8d8f93" stroke-width="0.7" fill="none"/></svg>www.moravel.co.nz<span class="social" aria-hidden="true"><i></i><i></i></span></li>
      </ul>
    </div>
  </section>
</main>
</body>
</html>
```